SkyvornQ Business Cards and Stationary Design

Need a design for our business cards and stationary. I want to carry on the theme of the logo. I want the business cards to have a design on the back. I would like the business cards and the stationary to carry the same theme, design scheme, and branding

Target Market(s)

Airlines and Maintenance Facilities

Industry/Entity Type

Aviation

Contact Information for Business Card

Name
Position Title
Address: 4827 Trellis Hollow Road, Fort Pierce, Florida, 34951
Office Number
Mobile Number
Email
Website

Font styles to use
Serif
Sans Serif

Colors

Designer to choose colors to be used in the design.

```html
<!DOCTYPE html>
<html lang="en">
<head>
<meta charset="utf-8">
<title>SkyvornQ Business Card</title>
<link href="https://fonts.googleapis.com/css2?family=Open+Sans:wght@400;600;700&display=swap" rel="stylesheet">
<style>
  :root {
    --navy: #14285a;
    --sky: #1a8fd6;
    --ink: #3a4558;
    --paper: #ffffff;
    --backdrop: #e4e5e7;
  }
  * { box-sizing: border-box; margin: 0; padding: 0; }
  html, body { width: 1200px; height: 852px; overflow: hidden; }
  body {
    background: var(--backdrop);
    font-family: "Open Sans", Arial, sans-serif;
    color: var(--ink);
    position: relative;
  }
  .card {
    position: absolute;
    top: 271px;
    width: 540px;
    height: 309px;
    background: var(--paper);
    border-radius: 18px;
    overflow: hidden;
    box-shadow: 0 6px 18px rgba(0,0,0,0.12);
  }
  .card--front { left: 40px; }
  .card--back { left: 620px; }

  .edge-band {
    position: absolute;
    left: 0; right: 0; bottom: 0;
    height: 8px;
    display: flex;
  }
  .edge-band__navy { flex: 0 0 46%; background: var(--navy); }
  .edge-band__sky { flex: 1; background: var(--sky); }

  .brand {
    display: flex;
    align-items: center;
    gap: 12px;
  }
  .brand__dot {
    width: 30px; height: 30px;
    border-radius: 50%;
    background: var(--sky);
  }
  .brand__name {
    font-weight: 700;
    color: var(--navy);
    text-transform: uppercase;
    letter-spacing: 0.14em;
  }

  /* Front */
  .card--front .brand {
    position: absolute;
    left: 0; right: 0; top: 112px;
    justify-content: center;
  }
  .card--front .brand__dot { width: 40px; height: 40px; }
  .card--front .brand__name { font-size: 40px; }
  .web-rule {
    position: absolute;
    left: 0; right: 0; top: 212px;
    display: flex;
    align-items: center;
    justify-content: center;
    gap: 14px;
  }
  .web-rule__line { width: 90px; height: 2px; background: var(--sky); }
  .web-rule__text { font-size: 13px; letter-spacing: 0.08em; color: var(--ink); }

  /* Back */
  .card--back .brand {
    position: absolute;
    right: 34px; top: 40px;
  }
  .card--back .brand__name { font-size: 26px; }
  .address {
    position: absolute;
    right: 34px; top: 150px;
    text-align: right;
    font-size: 12px;
    line-height: 1.5;
    color: var(--ink);
  }
  .person {
    position: absolute;
    left: 34px; top: 158px;
  }
  .person__name { font-size: 22px; font-weight: 600; color: var(--sky); line-height: 1.1; }
  .person__title { font-size: 12px; color: var(--ink); margin-top: 2px; }
  .contacts {
    list-style: none;
    margin-top: 10px;
    font-size: 12.5px;
    line-height: 1.55;
  }
  .contacts li { display: flex; align-items: center; gap: 9px; }
  .contacts svg { width: 12px; height: 12px; fill: var(--sky); flex: none; }
  .contacts .icon-globe { fill: none; stroke: var(--sky); stroke-width: 1.1; }
</style>
</head>
<body>

<section class="card card--front" aria-label="Card front">
  <div class="brand">
    <span class="brand__dot"></span>
    <span class="brand__name">SkyvornQ</span>
  </div>
  <div class="web-rule">
    <span class="web-rule__line"></span>
    <span class="web-rule__text">www.skyvornq.com</span>
    <span class="web-rule__line"></span>
  </div>
  <div class="edge-band"><span class="edge-band__navy"></span><span class="edge-band__sky"></span></div>
</section>

<section class="card card--back" aria-label="Card back">
  <div class="brand">
    <span class="brand__dot"></span>
    <span class="brand__name">SkyvornQ</span>
  </div>
  <p class="address">4827 Trellis Hollow Road,<br>Larkhaven, Ostrand 34951</p>

  <div class="person">
    <p class="person__name">Marla Venholt</p>
    <p class="person__title">Managing Director</p>
    <ul class="contacts">
      <li>
        <svg viewBox="0 0 12 12" aria-hidden="true"><path d="M2.5 0.8l2 2-1 1.3c.7 1.6 1.8 2.7 3.4 3.4l1.3-1 2 2-1.3 1.9C5.6 10.4 1.6 6.4 0.6 2.1z"/></svg>
        <span>4172 5096 318</span>
      </li>
      <li>
        <svg viewBox="0 0 12 12" aria-hidden="true"><path d="M3.5 0.5h5a1 1 0 0 1 1 1v9a1 1 0 0 1-1 1h-5a1 1 0 0 1-1-1v-9a1 1 0 0 1 1-1zM4 2v7h4V2z"/></svg>
        <span>6283 4410 925</span>
      </li>
      <li>
        <svg viewBox="0 0 12 12" aria-hidden="true"><path d="M0.5 2.5h11v7h-11zM1.5 3.3v.4L6 6.6l4.5-2.9v-.4z"/></svg>
        <span>marla@skyvornq.com</span>
      </li>
      <li>
        <svg class="icon-globe" viewBox="0 0 12 12" aria-hidden="true"><circle cx="6" cy="6" r="5"/><ellipse cx="6" cy="6" rx="2.2" ry="5"/><path d="M1 6h10"/></svg>
        <span>www.skyvornq.com</span>
      </li>
    </ul>
  </div>
  <div class="edge-band"><span class="edge-band__navy"></span><span class="edge-band__sky"></span></div>
</section>

</body>
</html>
```